Web Design

We need a website for a company based in Doha Qatar called
Lumara Maid Service.

It is the number one maid cleaning service company, and we have branches all over qatar.

Luxury Cleaning Service Provider.

The color scheme is gold, yellow and black like the logo.

Before they get to the website, there is an intro video.

The website should depict luxury.

Target Market(s)

People who need maids at their houses.

Industry/Entity Type

Cleaning Service

Requirements
Must have
• Luxury, Sleek, Modern

The opening sequence is a video which I already have. Its too big to upload here so I am going to put it on youtube.

After the opening sequence, the home page should have a widescreen photo background and it should change every five seconds, the first background photo should be of qatar westbay skyline. Then the second background should be of maid photos in cleaning positions. Then the third background should be of cleaner photos etc.

We will send you all the tabs and all the content later.

```html
<!DOCTYPE html>
<html lang="en">
<head>
<meta charset="utf-8">
<title>Lumara Maid Service</title>
<link href="https://fonts.googleapis.com/css2?family=Open+Sans:wght@400;600&display=swap" rel="stylesheet">
<style>
  :root {
    --white: #ffffff;
    --text-dark: #4a4a4a;
    --text-mid: #666666;
    --text-nav: #7a7a7a;
    --gold: #e3b52a;
    --gold-button: #e8bf35;
    --gold-shadow: #b48a12;
    --orange: #ee9a1e;
    --orange-dark: #d9810f;
    --brand-brown: #8a5a2e;
    --track: #8a949c;
    --track-fill: #3a4148;
    --dot: #d8d8d8;
    --dot-active: #f2c98a;
    --social-feed: #f07a1a;
    --social-one: #3b5a9a;
    --social-two: #2fa9e1;
  }
  * { margin: 0; padding: 0; box-sizing: border-box; }
  html, body { width: 1200px; height: 800px; overflow: hidden; background: var(--white); }
  body { font-family: "Open Sans", Arial, sans-serif; position: relative; }

  .site-header {
    position: absolute; left: 0; top: 0; width: 1200px; height: 153px;
    background: var(--white); box-shadow: 0 2px 6px rgba(0,0,0,0.08); z-index: 2;
  }
  .brand {
    position: absolute; left: 104px; top: 66px;
    display: flex; align-items: center; gap: 12px;
    font-size: 25px; font-weight: 600; color: var(--brand-brown);
  }
  .brand-mark { width: 16px; height: 16px; border-radius: 50%; background: var(--brand-brown); }
  .main-nav {
    position: absolute; right: 99px; top: 38px;
    display: flex; gap: 14px; font-size: 12.5px; color: var(--text-nav);
  }
  .call-us {
    position: absolute; right: 173px; top: 91px;
    font-size: 17.5px; font-weight: 600; color: var(--text-dark); letter-spacing: -0.3px;
  }
  .call-button {
    position: absolute; left: 1049px; top: 77px; width: 52px; height: 51px;
    background: linear-gradient(var(--orange), var(--orange-dark));
    border-radius: 2px; box-shadow: 0 2px 3px rgba(0,0,0,0.25);
    display: flex; align-items: center; justify-content: center;
  }

  .hero { position: absolute; left: 0; top: 153px; width: 1200px; height: 570px; background: var(--white); }
  .hero-photo {
    position: absolute; left: 0; top: 0; width: 676px; height: 570px;
    background: linear-gradient(90deg, #f1f2ef 0%, #e9ece6 12%, #efe7b8 30%, #dfe6ef 45%, #f1e98a 62%, #e8eef4 74%, #f4f6f7 90%, #ffffff 100%);
  }
  .hero-content { position: absolute; left: 588px; top: 0; width: 512px; }
  .hero-title {
    margin-top: 30px; padding-left: 12px; text-align: center;
    font-size: 24px; font-weight: 400; color: var(--text-mid);
  }
  .hero-text {
    margin: 8px auto 0; width: 500px; text-align: center;
    font-size: 13px; font-weight: 600; line-height: 19px; color: #5a5a5a;
  }
  .video { position: absolute; left: 0; top: 121px; width: 512px; }
  .video-screen {
    width: 512px; height: 278px; position: relative;
    background: linear-gradient(100deg, #2a2a2a 0%, #4a4a4a 35%, #6a6a6a 60%, #3a3a3a 100%);
  }
  .video-play {
    position: absolute; left: 235px; top: 124px; width: 44px; height: 42px;
    background: #111; display: flex; align-items: center; justify-content: center;
  }
  .video-controls {
    margin-top: 6px; height: 43px; background: var(--white);
    display: flex; align-items: center; font-size: 12px; color: var(--text-mid);
  }
  .control-play {
    width: 44px; height: 43px; background: var(--orange);
    display: flex; align-items: center; justify-content: center;
  }
  .time-current { margin-left: 12px; }
  .track { margin-left: 14px; width: 229px; height: 6px; background: var(--track); }
  .track-fill { width: 153px; height: 100%; background: var(--track-fill); }
  .time-total { margin-left: 14px; }
  .volume { margin-left: 9px; display: flex; align-items: center; gap: 6px; }
  .fullscreen { margin-left: 15px; }

  .enter-button {
    position: absolute; left: 748px; top: 478px; width: 220px; height: 39px;
    background: var(--gold-button); color: var(--white);
    font-size: 18px; font-weight: 600; text-align: center; line-height: 38px;
    box-shadow: 2px 2px 0 var(--gold-shadow);
  }
  .slider-dots { position: absolute; left: 600px; top: 548px; display: flex; gap: 7px; }
  .slider-dots span { width: 8px; height: 8px; border-radius: 50%; background: var(--dot); }
  .slider-dots span.active { background: var(--dot-active); }

  .site-footer {
    position: absolute; left: 0; top: 723px; width: 1200px; height: 77px; background: var(--gold);
  }
  .copyright { position: absolute; left: 102px; top: 31px; font-size: 13px; color: #4a3a18; }
  .social { position: absolute; left: 995px; top: 25px; display: flex; gap: 7px; }
  .social span {
    width: 30px; height: 30px; border-radius: 3px;
    box-shadow: inset 0 -3px 0 rgba(0,0,0,0.15), inset 0 12px 10px rgba(255,255,255,0.18);
  }
  .social .feed { background: var(--social-feed); margin-right: 3px; }
  .social .network-one { background: var(--social-one); }
  .social .network-two { background: var(--social-two); }
</style>
</head>
<body>
  <header class="site-header">
    <div class="brand"><span class="brand-mark"></span>Lumara Maid Service</div>
    <nav class="main-nav">
      <span>Home</span><span>|</span><span>About</span><span>|</span><span>Service</span>
    </nav>
    <div class="call-us">Call us - 028 - 47 - 1650</div>
    <div class="call-button">
      <svg width="24" height="24" viewBox="0 0 24 24" aria-hidden="true">
        <path fill="#ffffff" d="M6.6 10.8c1.4 2.8 3.8 5.1 6.6 6.6l2.2-2.2c.3-.3.7-.4 1-.2 1.1.4 2.3.6 3.6.6.6 0 1 .4 1 1V20c0 .6-.4 1-1 1C10.6 21 3 13.4 3 4c0-.6.4-1 1-1h3.5c.6 0 1 .4 1 1 0 1.3.2 2.5.6 3.6.1.3 0 .7-.2 1z"/>
      </svg>
    </div>
  </header>

  <main class="hero">
    <div class="hero-photo" role="img" aria-label="Smiling maid in a checked shirt and yellow gloves cleaning a bright window with a spray bottle and sponge"></div>
    <section class="hero-content">
      <h1 class="hero-title">Lorem ipsum dolor sit amet,</h1>
      <p class="hero-text">Nunc venenatis congue velit, eget eleifend sapien accumsan non. Sed blandit suscipit massa, eget egestas turpis consectetur</p>
      <div class="video">
        <div class="video-screen" role="img" aria-label="Black and white video still of a housekeeper holding folded towels">
          <div class="video-play">
            <svg width="10" height="12" viewBox="0 0 10 12" aria-hidden="true"><path fill="#ffffff" d="M0 0l10 6-10 6z"/></svg>
          </div>
        </div>
        <div class="video-controls">
          <div class="control-play">
            <svg width="9" height="11" viewBox="0 0 10 12" aria-hidden="true"><path fill="#ffffff" d="M0 0l10 6-10 6z"/></svg>
          </div>
          <span class="time-current">00:15:35</span>
          <div class="track"><div class="track-fill"></div></div>
          <span class="time-total">2:15:35</span>
          <div class="volume">
            <svg width="14" height="10" viewBox="0 0 14 10" aria-hidden="true">
              <path fill="#8a949c" d="M0 3h3l4-3v10L3 7H0z"/>
              <path fill="none" stroke="#8a949c" stroke-width="1.2" d="M9 3a3 3 0 0 1 0 4M11 1.5a5 5 0 0 1 0 7"/>
            </svg>
            <svg width="35" height="10" viewBox="0 0 35 10" aria-hidden="true">
              <g fill="#3fb6c8"><rect x="0" width="2" height="10"/><rect x="4" width="2" height="10"/><rect x="8" width="2" height="10"/><rect x="12" width="2" height="10"/><rect x="16" width="2" height="10"/></g>
              <g fill="#cfd4d8"><rect x="20" width="2" height="10"/><rect x="24" width="2" height="10"/><rect x="28" width="2" height="10"/><rect x="32" width="2" height="10"/></g>
            </svg>
          </div>
          <svg class="fullscreen" width="18" height="14" viewBox="0 0 18 14" aria-hidden="true">
            <g fill="none" stroke="#7a848c" stroke-width="1.5">
              <path d="M1 4V1h4M13 1h4v3M17 10v3h-4M5 13H1v-3"/>
              <rect x="5" y="4" width="8" height="6"/>
            </g>
          </svg>
        </div>
      </div>
    </section>
    <div class="enter-button">Enter Site</div>
    <div class="slider-dots"><span class="active"></span><span></span><span></span></div>
  </main>

  <footer class="site-footer">
    <p class="copyright">Copyright © 2014 lumaraservice.com&nbsp; All rights reserved</p>
    <div class="social" aria-label="Social links">
      <span class="feed"></span>
      <span class="network-one"></span>
      <span class="network-two"></span>
    </div>
  </footer>
</body>
</html>
```